RW Framewell Inc Business cards

We need business cards using our existing logo but slightly modified. Right now the logo says RW Loadbearing Masonry. We want to keep the RW part of the design, but replace the Structural Concrete portion with "FRAMEWELL". Please see the attached file.
Ideally this would be a blank template so we can add Different Names, titles, and phone numbers later.
On the one side we want only the logo and on the other side the detail. I'm attaching an example for you to see.
Please reach out with any other questions. Our address and other details will be given out once we find a design we like.

Target Market(s)

Construction Industry

```html
<!DOCTYPE html>
<html lang="en">
<head>
<meta charset="utf-8">
<title>RW Framewell Inc – Business Cards</title>
<link href="https://fonts.googleapis.com/css2?family=Michroma&family=Open+Sans:wght@400&display=swap" rel="stylesheet">
<style>
  :root {
    --page-bg: #1e1e1e;
    --brand-blue: #0f75bd;
    --logo-silver: #d4d6d8;
    --logo-grey: #7d7f82;
    --card-white: #ffffff;
    --text-grey: #6f7073;
    --rule-grey: #9a9a9a;
  }
  * { margin: 0; padding: 0; box-sizing: border-box; }
  html, body { width: 1200px; height: 900px; overflow: hidden; }
  body {
    background: var(--page-bg);
    display: flex;
    flex-direction: column;
    align-items: center;
    justify-content: center;
    gap: 40px;
    font-family: "Open Sans", sans-serif;
  }
  .card {
    width: 630px;
    height: 360px;
    position: relative;
  }
  .card--front {
    background: var(--brand-blue);
    display: flex;
    align-items: center;
    justify-content: center;
  }
  .card--back {
    background: var(--card-white);
    display: flex;
    align-items: center;
  }
  .wordmark {
    font-family: "Michroma", sans-serif;
    font-weight: 400;
    letter-spacing: 2px;
    white-space: nowrap;
  }
  .card--front .wordmark { color: var(--logo-silver); font-size: 36px; }
  .card--back .wordmark { color: var(--logo-grey); font-size: 21px; }
  .back-logo {
    width: 340px;
    padding-left: 34px;
  }
  .divider {
    width: 1px;
    height: 230px;
    background: var(--rule-grey);
    margin-right: 28px;
  }
  .details { color: var(--text-grey); }
  .person-name {
    font-family: "Michroma", sans-serif;
    color: var(--brand-blue);
    font-size: 19px;
    letter-spacing: 1px;
    line-height: 1.1;
  }
  .person-title { font-size: 17px; margin-bottom: 16px; }
  .contact-list { list-style: none; font-size: 17px; line-height: 1.5; }
  .contact-list li { display: flex; align-items: center; gap: 10px; }
  .contact-list svg { width: 16px; height: 16px; flex: none; fill: var(--brand-blue); }
  .address { font-size: 18px; line-height: 1.3; margin-top: 14px; }
</style>
</head>
<body>
  <section class="card card--front" aria-label="Card front">
    <div class="wordmark">RW FRAMEWELL</div>
  </section>

  <section class="card card--back" aria-label="Card back">
    <div class="back-logo"><div class="wordmark">RW FRAMEWELL</div></div>
    <div class="divider"></div>
    <div class="details">
      <div class="person-name">DANA WHITLOCK</div>
      <div class="person-title">Chief Officer</div>
      <ul class="contact-list">
        <li><svg viewBox="0 0 16 16"><path d="M3 1l3 3-1.5 2a9 9 0 0 0 5.5 5.5L12 10l3 3-2 2C7 15 1 9 1 3z"/></svg>+00 8 38 00 00</li>
        <li><svg viewBox="0 0 16 16"><path d="M4 0h8a1 1 0 0 1 1 1v14a1 1 0 0 1-1 1H4a1 1 0 0 1-1-1V1a1 1 0 0 1 1-1zm1 2v10h6V2z"/></svg>+00 0 90 00 00</li>
        <li><svg viewBox="0 0 16 16"><path d="M0 3h16v10H0zm1.5 1.2L8 9l6.5-4.8V12h-13z"/></svg>info@rwframewell.com</li>
        <li><svg viewBox="0 0 16 16"><path d="M8 0a8 8 0 1 0 0 16A8 8 0 0 0 8 0zm0 1.5c1 0 2 2 2.3 5H5.7C6 3.5 7 1.5 8 1.5zM5.7 9.5h4.6C10 12.5 9 14.5 8 14.5S6 12.5 5.7 9.5zM1.6 7.5h2.6v1H1.6zm10.2 0h2.6v1h-2.6z"/></svg>www.rwframewell.com</li>
      </ul>
      <p class="address">Your address line here<br>Country/ State</p>
    </div>
  </section>
</body>
</html>
```